Easy Marinade Labels for Butchery Store

Need a set of labels designed for a Butchery Shop. They will sit in the top left corner of the packets as a triangle (7cm each side). Easy because the only major requirement is the label name and some small text saying "Please ask in store to see spec sheet for ingredients". Extra points for finding a fun way to incorporate the logo and/or images of food (garlic bulbs, chilli, spices ect) to enhance the label. List of Marinade Names below: GarlicPepper Mint & RosemarySatayBBQChilli Plum & GingerSundried Tomato & BasilBuffaloHoney SoyHoi-SinPer PeriSpicy CajunTeriyakiBlack Bean Ive also attached the logo and an example of how the label might sit on a packet of meat. Thanks

Target Market(s)

Butchery Deli Shop Customers

Industry/Entity Type

Food Store

Font styles to use
Serif
Sans Serif
Decorative
Other font styles liked:
• Fun font that isn't a generic Quellbrix Font?

Colors

Designer to choose colors to be used in the design.

Requirements
Must have
• Product Name
• Small text saying "Please ask in store to see spec sheet for ingredients"
Nice to have
• Photos of ingredients that would match that type of marinade - Chilli, Garlic, Spices.
• Fenly Oak Logo - not essential if it doesn't look good on the label / doesn't fit.

```html
<!DOCTYPE html>
<html lang="en">
<head>
<meta charset="utf-8">
<title>Fenly Oak Marinade Labels</title>
<link rel="stylesheet" href="https://fonts.googleapis.com/css2?family=Aldrich&family=Cinzel:wght@700&family=Oswald:wght@300&display=swap">
<style>
  :root{
    --bg-centre:#ffffff;
    --bg-edge:#c9cdd1;
    --gold-light:#e8d98a;
    --gold-dark:#8a7440;
    --cream:#f5f2ea;
    --ink-gold:#a5781c;
    --ink-brown:#5b4a3a;
    --brand-red:#b01b1b;
    --tomato-red:#c8161d;
    --basil-green:#4fae4a;
    --garlic-mauve:#7a5a60;
    --garlic-tone:#e9e0c9;
    --peri-red:#c9241a;
    --peri-orange:#f07a1a;
    --bean-black:#262626;
    --bean-green:#2e8a3e;
    --pepper-black:#2a2a2a;
    --pepper-silver:#b9b9b9;
    --mint-teal:#7fc9aa;
    --mint-pale:#bfe6d3;
  }
  html,body{margin:0;padding:0;overflow:hidden;}
  body{width:1200px;height:923px;}
  .sheet{
    position:relative;width:1200px;height:923px;overflow:hidden;
    background:radial-gradient(ellipse at 50% 45%,var(--bg-centre) 40%,var(--bg-edge) 100%);
  }
  .label{position:absolute;width:446px;height:221px;}
  .label--col1{left:126px;}
  .label--col2{left:627px;}
  .label--row1{top:109px;}
  .label--row2{top:349px;}
  .label--row3{top:593px;}
  .label svg{display:block;width:100%;height:100%;overflow:visible;}
  .frame-outer{fill:url(#gold);}
  .frame-fill{fill:var(--cream);}
  .brand{font-family:"Cinzel",serif;font-weight:700;font-size:24px;fill:var(--brand-red);text-anchor:middle;}
  .intro{font-family:"Aldrich",sans-serif;font-size:14px;fill:var(--ink-gold);text-anchor:middle;}
  .flavour{font-family:"Aldrich",sans-serif;font-size:29px;fill:var(--ink-gold);text-anchor:middle;}
  .note{font-family:"Oswald",sans-serif;font-weight:300;font-size:15px;fill:var(--ink-brown);text-anchor:middle;}
  .note--small{font-size:14px;}
</style>
</head>
<body>
<main class="sheet">

  <svg width="0" height="0" style="position:absolute" aria-hidden="true">
    <defs>
      <linearGradient id="gold" x1="0" y1="0" x2="1" y2="1">
        <stop offset="0" stop-color="var(--gold-dark)"/>
        <stop offset="0.5" stop-color="var(--gold-light)"/>
        <stop offset="1" stop-color="var(--gold-dark)"/>
      </linearGradient>
    </defs>
  </svg>

  <!-- Sundried Tomato & Basil -->
  <div class="label label--col1 label--row1">
    <svg viewBox="0 0 485 240">
      <polygon class="frame-outer" points="242.5,0 485,240 0,240"/>
      <polygon style="fill:var(--tomato-red)" points="242.5,8.5 470.5,234 14.5,234"/>
      <polygon style="fill:var(--basil-green)" points="242.5,14.1 460.9,230 24.1,230"/>
      <polygon class="frame-fill" points="242.5,18.4 453.6,227 31.4,227"/>
      <g role="img" aria-label="Tomato with basil leaves illustration">
        <ellipse cx="242" cy="68" rx="36" ry="24" fill="var(--tomato-red)" opacity="0.85"/>
      </g>
      <text class="brand" x="242" y="118" textLength="140" lengthAdjust="spacingAndGlyphs">Fenly Oak</text>
      <text class="intro" x="242" y="150" textLength="176" lengthAdjust="spacing">MARINATED WITH</text>
      <text class="flavour" x="242" y="180" textLength="256" lengthAdjust="spacingAndGlyphs">SUNDRIED TOMATO</text>
      <text class="flavour" x="242" y="206" textLength="112" lengthAdjust="spacingAndGlyphs">&amp; BASIL</text>
      <text class="note" x="242" y="223" textLength="295" lengthAdjust="spacingAndGlyphs">Please ask in store to see spec sheet for ingredients</text>
    </svg>
  </div>

  <!-- Garlic Sprinkle -->
  <div class="label label--col2 label--row1">
    <svg viewBox="0 0 485 240">
      <polygon class="frame-outer" points="242.5,0 485,240 0,240"/>
      <polygon style="fill:var(--garlic-mauve)" points="242.5,12 463,231 22,231"/>
      <polygon class="frame-fill" points="242.5,17 455,228 30,228"/>
      <g role="img" aria-label="Garlic bulbs and cloves illustration">
        <ellipse cx="242" cy="66" rx="38" ry="28" fill="var(--garlic-tone)"/>
      </g>
      <text class="brand" x="242" y="120" textLength="140" lengthAdjust="spacingAndGlyphs">Fenly Oak</text>
      <text class="intro" x="242" y="166" textLength="178" lengthAdjust="spacing">MARINATED WITH</text>
      <text class="flavour" x="242" y="194" textLength="240" lengthAdjust="spacingAndGlyphs">GARLIC SPRINKLE</text>
      <text class="note" x="242" y="223" textLength="295" lengthAdjust="spacingAndGlyphs">Please ask in store to see spec sheet for ingredients</text>
    </svg>
  </div>

  <!-- Peri Peri -->
  <div class="label label--col1 label--row2">
    <svg viewBox="0 0 485 240">
      <polygon class="frame-outer" points="242.5,0 485,240 0,240"/>
      <polygon style="fill:var(--peri-red)" points="242.5,8.5 470.5,234 14.5,234"/>
      <polygon style="fill:var(--peri-orange)" points="242.5,14.1 460.9,230 24.1,230"/>
      <polygon class="frame-fill" points="242.5,18.4 453.6,227 31.4,227"/>
      <g role="img" aria-label="Red chillies with garlic illustration">
        <ellipse cx="245" cy="70" rx="38" ry="22" fill="var(--peri-red)" opacity="0.8"/>
      </g>
      <text class="brand" x="242" y="120" textLength="140" lengthAdjust="spacingAndGlyphs">Fenly Oak</text>
      <text class="intro" x="242" y="167" textLength="176" lengthAdjust="spacing">MARINATED WITH</text>
      <text class="flavour" x="242" y="196" textLength="135" lengthAdjust="spacingAndGlyphs">PERI PERI</text>
      <text class="note" x="242" y="223" textLength="295" lengthAdjust="spacingAndGlyphs">Please ask in store to see spec sheet for ingredients</text>
    </svg>
  </div>

  <!-- Black Bean Sauce -->
  <div class="label label--col2 label--row2">
    <svg viewBox="0 0 485 240">
      <polygon class="frame-outer" points="242.5,0 485,240 0,240"/>
      <polygon style="fill:var(--bean-black)" points="242.5,8.5 470.5,234 14.5,234"/>
      <polygon style="fill:var(--bean-green)" points="242.5,14.1 460.9,230 24.1,230"/>
      <polygon class="frame-fill" points="242.5,18.4 453.6,227 31.4,227"/>
      <g role="img" aria-label="Black beans illustration">
        <ellipse cx="242" cy="66" rx="34" ry="28" fill="var(--bean-black)"/>
      </g>
      <text class="brand" x="242" y="120" textLength="140" lengthAdjust="spacingAndGlyphs">Fenly Oak</text>
      <text class="intro" x="242" y="167" textLength="176" lengthAdjust="spacing">MARINATED WITH</text>
      <text class="flavour" x="242" y="196" textLength="266" lengthAdjust="spacingAndGlyphs">BLACK BEAN SAUCE</text>
      <text class="note" x="242" y="223" textLength="295" lengthAdjust="spacingAndGlyphs">Please ask in store to see spec sheet for ingredients</text>
    </svg>
  </div>

  <!-- Pepper Sprinkle -->
  <div class="label label--col1 label--row3">
    <svg viewBox="0 0 485 240">
      <polygon class="frame-outer" points="242.5,0 485,240 0,240"/>
      <polygon style="fill:var(--pepper-black)" points="242.5,8.5 470.5,234 14.5,234"/>
      <polygon style="fill:var(--pepper-silver)" points="242.5,14.1 460.9,230 24.1,230"/>
      <polygon class="frame-fill" points="242.5,18.4 453.6,227 31.4,227"/>
      <g role="img" aria-label="Pepper shaker illustration">
        <ellipse cx="242" cy="68" rx="30" ry="26" fill="var(--pepper-black)"/>
      </g>
      <text class="brand" x="242" y="122" textLength="140" lengthAdjust="spacingAndGlyphs">Fenly Oak</text>
      <text class="intro" x="242" y="166" textLength="176" lengthAdjust="spacing">MARINATED WITH</text>
      <text class="flavour" x="242" y="195" textLength="250" lengthAdjust="spacingAndGlyphs">PEPPER SPRINKLE</text>
      <text class="note note--small" x="242" y="223" textLength="262" lengthAdjust="spacingAndGlyphs">Please ask in store to see spec sheet for ingredients</text>
    </svg>
  </div>

  <!-- Mint & Rosemary -->
  <div class="label label--col2 label--row3">
    <svg viewBox="0 0 485 240">
      <polygon class="frame-outer" points="242.5,0 485,240 0,240"/>
      <polygon style="fill:var(--mint-teal)" points="242.5,8.5 470.5,234 14.5,234"/>
      <polygon style="fill:var(--mint-pale)" points="242.5,14.1 460.9,230 24.1,230"/>
      <polygon class="frame-fill" points="242.5,18.4 453.6,227 31.4,227"/>
      <g role="img" aria-label="Mint leaves and rosemary sprigs illustration">
        <ellipse cx="245" cy="66" rx="40" ry="26" fill="var(--mint-teal)" opacity="0.8"/>
      </g>
      <text class="brand" x="242" y="122" textLength="140" lengthAdjust="spacingAndGlyphs">Fenly Oak</text>
      <text class="intro" x="242" y="166" textLength="176" lengthAdjust="spacing">MARINATED WITH</text>
      <text class="flavour" x="242" y="195" textLength="262" lengthAdjust="spacingAndGlyphs">MINT &amp; ROSEMARY</text>
      <text class="note" x="242" y="223" textLength="295" lengthAdjust="spacingAndGlyphs">Please ask in store to see spec sheet for ingredients</text>
    </svg>
  </div>

</main>
</body>
</html>
```